Business Card Design Project

Doctor, Pain Management. Need a new business card design with appointment info on the back. New address is 18 Corvell Road, Suite 304, Brisdale, NJ 07391. Right now I believe the rest of the information is staying the same.

```html
<!DOCTYPE html>
<html lang="en">
<head>
<meta charset="utf-8">
<title>Harborline Pain Care – Business Card</title>
<link rel="stylesheet" href="https://fonts.googleapis.com/css2?family=Open+Sans:wght@400;600;700&display=swap">
<style>
  :root {
    --orange: #ea5b0f;
    --ink: #222222;
    --grey-text: #8a8a8a;
    --rule: #9a9a9a;
    --card-front: #f3f3f3;
    --card-back: #ffffff;
    --stage: #303030;
    --dark-band: #262626;
  }
  * { margin: 0; padding: 0; box-sizing: border-box; }
  html, body { width: 1200px; height: 1200px; overflow: hidden; }
  body {
    background: var(--stage);
    font-family: "Open Sans", Arial, sans-serif;
    color: var(--ink);
    position: relative;
  }
  .card {
    position: absolute;
    top: 310px;
    height: 594px;
    overflow: hidden;
  }
  .card-front { left: 234px; width: 364px; background: var(--card-front); }
  .card-back { left: 627px; width: 369px; background: var(--card-back); }

  /* front */
  .brand-small {
    position: absolute; top: 94px; left: 0; right: 0;
    display: flex; justify-content: center; align-items: center; gap: 10px;
  }
  .brand-mark-small { width: 16px; height: 16px; border-radius: 50%; background: var(--orange); }
  .brand-word-small { font-weight: 700; font-size: 44px; line-height: 1; color: var(--ink); letter-spacing: 1px; }
  .practice-name {
    position: absolute; top: 180px; left: 0; right: 0; text-align: center;
    font-size: 24px; font-weight: 400; color: var(--ink);
  }
  .doctor-name {
    position: absolute; top: 294px; left: 0; right: 0; text-align: center;
    font-size: 21px; font-weight: 700; color: var(--orange);
  }
  .doctor-name .surname { color: var(--ink); }
  .doctor-title {
    position: absolute; top: 321px; left: 0; right: 0; text-align: center;
    font-size: 16px; color: var(--ink);
  }
  .icon-row {
    position: absolute; top: 364px; left: 58px; width: 253px; height: 22px;
    display: flex; align-items: center; gap: 6px;
  }
  .icon-row .rule { flex: 1; height: 1px; background: var(--ink); }
  .icon-row .icons { display: flex; gap: 6px; margin: 0 2px; }
  .icon-box { width: 22px; height: 22px; background: var(--orange); display: block; }
  .contact-list {
    position: absolute; top: 396px; left: 0; right: 0; text-align: center;
    font-size: 15.5px; line-height: 21.5px; list-style: none;
  }
  .divider {
    position: absolute; top: 493px; left: 58px; width: 253px; height: 1px; background: var(--ink);
  }
  .address {
    position: absolute; top: 504px; left: 0; right: 0; text-align: center;
    font-size: 15.5px; line-height: 21.5px; font-style: normal;
  }

  /* back */
  .brand-large {
    position: absolute; top: 70px; left: 0; right: 0;
    display: flex; justify-content: center; align-items: center; gap: 16px;
  }
  .brand-mark-large { width: 34px; height: 34px; border-radius: 50%; background: var(--orange); }
  .brand-word-large { font-weight: 700; font-size: 108px; line-height: 1; color: var(--ink); letter-spacing: 2px; }
  .appointment-band {
    position: absolute; top: 236px; left: 0; right: 0; height: 62px;
    background: var(--orange); color: #fff;
    display: flex; align-items: center; justify-content: center;
    font-size: 26px; font-weight: 600; letter-spacing: 0.5px;
  }
  .field {
    position: absolute; left: 28px; width: 314px; height: 30px;
    border-bottom: 1.5px solid var(--rule);
    font-size: 23px; line-height: 26px; color: var(--grey-text);
  }
  .field-name { top: 324px; }
  .field-date { top: 383px; }
  .field-time { top: 443px; }
  .notice-band {
    position: absolute; top: 510px; left: 0; right: 0; height: 56px;
    background: var(--dark-band); color: var(--orange);
    display: flex; align-items: center; justify-content: center; text-align: center;
    font-size: 15px; line-height: 23px;
  }
</style>
</head>
<body>

<section class="card card-front" aria-label="Business card front">
  <div class="brand-small">
    <span class="brand-mark-small"></span>
    <span class="brand-word-small">HPC</span>
  </div>
  <p class="practice-name">Harborline Pain Care</p>
  <h1 class="doctor-name">DR. MEILIN <span class="surname">TAO</span>, M.D., PH.D.</h1>
  <p class="doctor-title">Board Certified Anesthiologist</p>

  <div class="icon-row">
    <span class="rule"></span>
    <span class="icons">
      <svg class="icon-box" viewBox="0 0 22 22" aria-label="Phone">
        <rect width="22" height="22" fill="#ea5b0f"/>
        <path d="M5 8 Q11 4 17 8 L16 10 L13 9 L13 8 Q11 7 9 8 L9 9 L6 10 Z" fill="#fff"/>
        <rect x="7" y="11" width="8" height="6" rx="1" fill="#fff"/>
      </svg>
      <svg class="icon-box" viewBox="0 0 22 22" aria-label="Fax">
        <rect width="22" height="22" fill="#ea5b0f"/>
        <rect x="7" y="4" width="8" height="4" fill="#fff"/>
        <rect x="4" y="9" width="14" height="6" rx="1" fill="#fff"/>
        <rect x="7" y="13" width="8" height="5" fill="#fff" stroke="#ea5b0f" stroke-width="1"/>
      </svg>
      <svg class="icon-box" viewBox="0 0 22 22" aria-label="Website">
        <rect width="22" height="22" fill="#ea5b0f"/>
        <circle cx="11" cy="11" r="6.5" fill="#fff"/>
        <path d="M8 8 Q10 9 9 11 Q11 13 10 15 M13 7 Q12 10 15 11" stroke="#ea5b0f" stroke-width="1.4" fill="none"/>
      </svg>
      <svg class="icon-box" viewBox="0 0 22 22" aria-label="Email">
        <rect width="22" height="22" fill="#ea5b0f"/>
        <rect x="4.5" y="6.5" width="13" height="9" fill="#fff"/>
        <path d="M4.5 6.5 L11 12 L17.5 6.5" stroke="#ea5b0f" stroke-width="1.3" fill="none"/>
      </svg>
    </span>
    <span class="rule"></span>
  </div>

  <ul class="contact-list">
    <li>973.555.0148</li>
    <li>973.555.0162</li>
    <li>www.harborlinepc.com</li>
    <li>care.service@harborlinepc.com</li>
  </ul>
  <div class="divider"></div>
  <address class="address">18 Corvell Road, Suite 304<br>Brisdale, NJ 07391</address>
</section>

<section class="card card-back" aria-label="Business card back">
  <div class="brand-large">
    <span class="brand-mark-large"></span>
    <span class="brand-word-large">HPC</span>
  </div>
  <div class="appointment-band">APPOINTMENT</div>
  <div class="field field-name">NAME:</div>
  <div class="field field-date">DATE :</div>
  <div class="field field-time">TIME :</div>
  <div class="notice-band">If unable to keep your appointment,<br>please contact us as soon as possible</div>
</section>

</body>
</html>
```